BRIGHTHOLD PROPERTY MANAGEMENT INC. WEBSITE

Please make the website more family-friendly.

I want a website to help me build my property management business by adding listing properties and creating an online application. Im open to any other ideas.
I want a WordPress designer to code it.

Here is my current website. www.brighthold.biz

IDEA: I like the website design https://www.pelicanclimateservices.com/

Thank you

Tom

Number of Pages Required

5+ page

```html
<!DOCTYPE html>
<html lang="en">
<head>
<meta charset="utf-8">
<title>Brighthold Property Management</title>
<link href="https://fonts.googleapis.com/css2?family=Inter:wght@400;500;600;700&family=Poppins:wght@400;500;600&display=swap" rel="stylesheet">
<style>
:root{
  --red:#a2262b;
  --red-dark:#8c1f23;
  --ink:#2b2b2b;
  --text:#555;
  --muted:#9a9a9a;
  --line:#e3e3e3;
  --soft:#f4ecea;
  --footer:#2e2e2e;
  --gold:#f2c230;
}
*{box-sizing:border-box;margin:0;padding:0}
html,body{width:1200px;height:5249px;overflow:hidden}
body{position:relative;background:#fff;font-family:"Poppins",sans-serif;color:var(--text)}
.abs{position:absolute}
h1,h2,h3{font-family:"Inter",sans-serif;color:var(--ink)}
.tag{position:absolute;color:var(--red);font-size:15px}
.heading{position:absolute;font-size:31px;font-weight:700;line-height:38px}
.para{position:absolute;font-size:13.5px;line-height:22.5px;color:#555}

/* header */
.topbar{position:absolute;top:0;left:0;width:1200px;height:68px;background:#f7f7f7}
.brand{position:absolute;left:98px;top:22px;display:flex;align-items:center;gap:8px;color:var(--red);font-family:"Inter",sans-serif;font-weight:700;font-size:17px}
.brand i{display:block;width:14px;height:14px;background:var(--red)}
.contact-top{position:absolute;top:25px;font-size:13px;color:#333;display:flex;align-items:center;gap:6px}
.nav{position:absolute;top:68px;left:0;width:1200px;height:36px;border-bottom:1px solid var(--line);font-size:11px;color:#777}
.nav a{position:absolute;top:10px;text-decoration:none;color:#888}
.nav a.active{color:#222;font-weight:600}

/* hero */
.hero{position:absolute;top:104px;left:0;width:1200px;height:536px;background:linear-gradient(180deg,#5c5566 0%,#6d5d68 45%,#4a433f 75%,#7d7a63 100%)}
.hero h1{position:absolute;top:190px;width:1200px;text-align:center;color:#fff;font-size:49px;font-weight:700;font-family:"Poppins",sans-serif}
.hero p{position:absolute;top:272px;width:1200px;text-align:center;color:#fff;font-size:28px}
.search{position:absolute;top:388px;left:349px;width:500px;height:51px;background:#fff;border-radius:26px;overflow:hidden}
.search span{position:absolute;left:26px;top:16px;font-size:14px;color:#b4b4b4}
.search b{position:absolute;right:0;top:0;width:66px;height:51px;background:var(--red);border-radius:26px}

/* about */
.photo{position:absolute;border-radius:2px}

/* listings */
.tabs{position:absolute;left:98px;top:1260px;width:335px;height:60px;border:1.5px solid var(--red);border-radius:4px;overflow:hidden;font-size:19px}
.tabs span{position:absolute;top:0;height:100%;width:50%;text-align:center;line-height:58px}
.tab-on{left:0;background:var(--red);color:#fff}
.tab-off{right:0;color:#999}
.divider{position:absolute;left:98px;top:1343px;width:1004px;height:1px;background:var(--line)}
.select{position:absolute;top:1368px;height:50px;border:1.5px solid #bbb;border-radius:4px;font-size:18px;color:#333;padding:12px 0 0 14px}
.select svg{position:absolute;right:14px;top:19px}
.btn-filter{position:absolute;left:469px;top:1368px;width:131px;height:50px;background:var(--red);color:#fff;border-radius:4px;font-size:18px;text-align:center;line-height:50px}
.card{position:absolute;top:1458px;width:314px;height:666px;border:1.5px solid #ccc;background:#fff}
.card .pic{position:absolute;left:0;top:0;width:100%;height:362px}
.card .badge{position:absolute;left:0;top:362px;width:100%;height:16px;background:#f7e39b;font-size:9px;color:#6a5a00;padding-left:10px;line-height:16px}
.card .price{position:absolute;left:28px;top:392px;font-size:19px;font-weight:600;color:var(--red-dark)}
.card .heart{position:absolute;right:96px;top:393px}
.card .type{position:absolute;left:28px;top:424px;font-size:19px;font-weight:600;color:#222}
.card .addr{position:absolute;left:28px;top:460px;font-size:11px;color:#999}
.card .feats{position:absolute;left:28px;top:506px;font-size:10px;color:#777;display:flex;gap:14px}
.card .feats span{display:flex;align-items:center;gap:5px}
.card .book{position:absolute;left:28px;top:556px;width:254px;height:40px;border:1.5px solid var(--red);border-radius:4px;color:var(--red);font-size:12px;text-align:center;line-height:37px}
.card .more{position:absolute;left:28px;top:608px;width:254px;height:40px;border:1.5px solid #bbb;border-radius:4px;color:#aaa;font-size:12px;text-align:center;line-height:37px}
.pager{position:absolute;left:893px;top:2168px;display:flex;gap:14px;align-items:center;font-size:12px}
.pager span{width:24px;height:24px;background:#eee;color:#777;text-align:center;line-height:24px;border-radius:2px}
.pager span.on{background:var(--red);color:#fff}

.btn-red{position:absolute;background:var(--red);color:#fff;border-radius:4px;font-size:14px;text-align:center}

/* why us */
.center-tag{position:absolute;width:1200px;text-align:center}
.pill{position:absolute;height:62px;background:#fff;border:2px solid var(--red);border-radius:32px;box-shadow:0 4px 10px rgba(0,0,0,.12);display:flex;align-items:center;justify-content:center;gap:14px;color:var(--red);font-size:13px;line-height:17px;text-align:center}

/* contact form */
.form-card{position:absolute;left:718px;top:3685px;width:386px;height:477px;background:#fff;box-shadow:0 2px 14px rgba(0,0,0,.1);border-radius:4px}
.form-card label{position:absolute;left:26px;font-size:12px;color:#333}
.form-card .field{position:absolute;left:26px;width:332px;height:40px;border:1px solid #e6e6e6;border-radius:3px;font-size:11px;color:#888;padding:11px 14px}
.form-card .submit{position:absolute;left:26px;top:403px;width:332px;height:50px;background:var(--red);color:#fff;border-radius:5px;font-size:13px;font-weight:600;text-align:center;line-height:50px}

/* testimonials */
.quote{position:absolute;top:4444px;width:273px;height:202px;border:1px solid #e6e6e6;background:#fff}
.quote .stars{position:absolute;left:28px;top:26px;color:var(--gold);font-size:18px;letter-spacing:3px}
.quote p{position:absolute;left:28px;top:64px;width:200px;font-size:10.5px;line-height:19px;color:#777}
.quote .avatar{position:absolute;left:28px;top:144px;width:38px;height:38px;border-radius:50%}
.quote .who{position:absolute;left:82px;top:147px;font-size:10px;line-height:18px;color:#555}
.quote .who b{color:var(--red);font-weight:400}
.arrow{position:absolute;top:4524px;width:40px;height:40px;border-radius:50%;background:#9c9c9c}

/* footer */
.footer{position:absolute;left:0;top:4736px;width:1200px;height:513px;background:var(--footer);color:#e8e8e8}
.footer .name{position:absolute;left:112px;top:96px;display:flex;align-items:center;gap:10px;font-family:"Inter",sans-serif;font-size:26px;font-weight:700;color:#fff}
.footer .name i{width:22px;height:22px;background:var(--red);display:block}
.footer h4{position:absolute;font-size:14px;font-weight:600;color:#fff}
.footer ul{position:absolute;list-style:none;font-size:12px;line-height:33px;color:#ddd}
.social{position:absolute;top:148px;display:block;width:22px;height:22px;background:#fff;border-radius:4px}
.footer .rule{position:absolute;left:98px;top:224px;width:1004px;height:1px;background:#666}
.sub-input{position:absolute;left:730px;top:310px;width:251px;height:39px;background:#fff;color:#888;font-size:11px;padding:12px 16px}
.sub-btn{position:absolute;left:985px;top:310px;width:117px;height:39px;background:var(--red);color:#fff;font-size:12px;text-align:center;line-height:39px}
.copy{position:absolute;right:98px;top:484px;font-size:11px;color:#aaa}
.fcontact{position:absolute;left:424px;font-size:12px;line-height:15px;display:flex;gap:14px;color:#ddd}
</style>
</head>
<body>

<header>
  <div class="topbar">
    <div class="brand"><i></i>BRIGHTHOLD</div>
    <div class="contact-top" style="left:706px">
      <svg width="14" height="14" viewBox="0 0 24 24"><path fill="#333" d="M6.6 10.8a15 15 0 0 0 6.6 6.6l2.2-2.2a1 1 0 0 1 1-.25 11.4 11.4 0 0 0 3.6.6 1 1 0 0 1 1 1V20a1 1 0 0 1-1 1A17 17 0 0 1 3 4a1 1 0 0 1 1-1h3.5a1 1 0 0 1 1 1c0 1.25.2 2.45.6 3.6a1 1 0 0 1-.25 1z"/></svg>(555) 214-7730</div>
    <div class="contact-top" style="left:864px">
      <svg width="15" height="12" viewBox="0 0 24 18"><rect width="24" height="18" rx="2" fill="#333"/><path d="M2 2l10 8 10-8" stroke="#fff" stroke-width="2" fill="none"/></svg>tomwhit23@mailbox.com
      <svg width="13" height="13" viewBox="0 0 24 24" style="margin-left:4px"><circle cx="12" cy="7" r="5" fill="#333"/><path d="M2 23a10 9 0 0 1 20 0z" fill="#333"/></svg>Login</div>
  </div>
  <nav class="nav">
    <a class="active" style="left:224px">Home</a>
    <a style="left:308px">About</a>
    <a style="left:392px">Listings ⌄</a>
    <a style="left:494px">Owners ⌄</a>
    <a style="left:597px">Prospect Tenants ⌄</a>
    <a style="left:755px">Community ⌄</a>
    <a style="left:880px">Mortgage Info ⌄</a>
  </nav>
</header>

<section class="hero" role="img" aria-label="Modern two-storey family house at dusk with lit garage">
  <h1>Welcome to Brighthold</h1>
  <p>Expert Property Management for Stress-Free Living</p>
  <div class="search">
    <span>Enter address, city, zip, neighborhood, or #MLS</span>
    <b><svg width="66" height="51" viewBox="0 0 66 51"><circle cx="31" cy="23" r="8" stroke="#fff" stroke-width="2.5" fill="none"/><path d="M37 29l6 6" stroke="#fff" stroke-width="2.5"/></svg></b>
  </div>
</section>

<section class="about">
  <span class="tag" style="left:98px;top:706px">About Us</span>
  <h2 class="heading" style="left:98px;top:734px">Sacramento, Elk Grove<br>Property Management</h2>
  <p class="para" style="left:98px;top:820px;width:465px">Our vision for Brighthold Property Management is to provide the best Property Management Services to the Sacramento and surrounding areas. I am focused on providing a more personalized service to you and your tenants. This means we are a one-stop-shop. You only deal with me, no middle guy, so no time is wasted.</p>
  <p class="para" style="left:98px;top:978px;width:465px">Brighthold Property Management is operated and owned by me Tom Whitaker I have over 10 years of experience in property management combined with real estate appraising and understand the importance of 'return on investment.'</p>
  <div class="photo" style="left:676px;top:700px;width:425px;height:388px;background:linear-gradient(180deg,#bcd0e0 0%,#d8d4cb 45%,#7b9a5a 85%,#a8211f 100%)" role="img" aria-label="House with a red for-rent sign on the front lawn"></div>
</section>

<section class="listings">
  <div class="tabs"><span class="tab-on">List</span><span class="tab-off">Map</span></div>
  <div class="divider"></div>
  <div class="select" style="left:100px;width:171px">Select Type<svg width="14" height="9" viewBox="0 0 14 9"><path d="M1 1l6 6 6-6" stroke="#333" stroke-width="1.6" fill="none"/></svg></div>
  <div class="select" style="left:285px;width:172px">Select Price<svg width="14" height="9" viewBox="0 0 14 9"><path d="M1 1l6 6 6-6" stroke="#333" stroke-width="1.6" fill="none"/></svg></div>
  <div class="btn-filter">Set filters</div>

  <article class="card" style="left:102px">
    <div class="pic" role="img" aria-label="Two-storey stone and siding house with green lawn" style="background:linear-gradient(180deg,#dfe8ef 0%,#c9c2b3 50%,#6f9a3e 100%)"></div>
    <div class="badge">✦ Available now</div>
    <div class="price">$700</div>
    <svg class="heart" width="22" height="22" viewBox="0 0 22 22"><circle cx="11" cy="11" r="10.5" fill="#fff" stroke="#ddd"/><path d="M11 15.5l-4-4a2.4 2.4 0 0 1 4-2.6 2.4 2.4 0 0 1 4 2.6z" stroke="var(--red)" stroke-width="1.3" fill="none"/></svg>
    <div class="type">Type A01</div>
    <div class="addr">1840 Maple Crest, Highland Lake, FL</div>
    <div class="feats"><span>▭ 3 Rooms</span><span>◇ 3 Bathrooms</span><span>⌂ 12×5m²</span></div>
    <div class="book">Book Now</div>
    <div class="more">More details</div>
  </article>
  <article class="card" style="left:444px">
    <div class="pic" role="img" aria-label="White cottage with dark tiled roof under blue sky" style="background:linear-gradient(180deg,#a9cdec 0%,#d9dfe3 40%,#7f8790 55%,#eceae2 80%,#dcdcd8 100%)"></div>
    <div class="badge">✦ Available now</div>
    <div class="price">$700</div>
    <svg class="heart" width="22" height="22" viewBox="0 0 22 22"><circle cx="11" cy="11" r="10.5" fill="#fff" stroke="#ddd"/><path d="M11 15.5l-4-4a2.4 2.4 0 0 1 4-2.6 2.4 2.4 0 0 1 4 2.6z" stroke="var(--red)" stroke-width="1.3" fill="none"/></svg>
    <div class="type">Type A01</div>
    <div class="addr">1840 Maple Crest, Highland Lake, FL</div>
    <div class="feats"><span>▭ 3 Rooms</span><span>◇ 3 Bathrooms</span><span>⌂ 12×5m²</span></div>
    <div class="book">Book Now</div>
    <div class="more">More details</div>
  </article>
  <article class="card" style="left:786px">
    <div class="pic" role="img" aria-label="Grey suburban house with garage and front lawn" style="background:linear-gradient(180deg,#a7cbe8 0%,#c6d6e2 40%,#6d7178 60%,#7ea34a 100%)"></div>
    <div class="badge">✦ Available now</div>
    <div class="price">$700</div>
    <svg class="heart" width="22" height="22" viewBox="0 0 22 22"><circle cx="11" cy="11" r="10.5" fill="#fff" stroke="#ddd"/><path d="M11 15.5l-4-4a2.4 2.4 0 0 1 4-2.6 2.4 2.4 0 0 1 4 2.6z" stroke="var(--red)" stroke-width="1.3" fill="none"/></svg>
    <div class="type">Type A01</div>
    <div class="addr">1840 Maple Crest, Highland Lake, FL</div>
    <div class="feats"><span>▭ 3 Rooms</span><span>◇ 3 Bathrooms</span><span>⌂ 12×5m²</span></div>
    <div class="book">Book Now</div>
    <div class="more">More details</div>
  </article>

  <div class="pager">
    <svg width="10" height="14" viewBox="0 0 10 14"><path d="M9 0v14L0 7z" fill="#333"/></svg>
    <span class="on">1</span><span>2</span><span>3</span><span>4</span>
    <svg width="10" height="14" viewBox="0 0 10 14"><path d="M1 0v14l9-7z" fill="#333"/></svg>
  </div>
</section>

<section class="apply">
  <span class="tag" style="left:98px;top:2344px">Tenant Applications</span>
  <h2 class="heading" style="left:98px;top:2372px">Apply to Rent with Brighthold:<br>Your New Home Awaits</h2>
  <p class="para" style="left:98px;top:2456px;width:495px">Our vision for Brighthold Property Management is to provide the best Property Management Services to the Sacramento and surrounding areas. I am focused on providing a more personalized service to you and your tenants. This means we are a one-stop-shop. You only deal with me, no middle guy, so no time is wasted.</p>
  <p class="para" style="left:98px;top:2592px;width:495px">Brighthold Property Management is operated and owned by me Tom Whitaker I have over 10 years of experience in property management combined with real estate appraising and understand the importance of 'return on investment.'</p>
  <div class="btn-red" style="left:98px;top:2716px;width:168px;height:52px;line-height:52px">Apply now</div>
  <div class="photo" style="left:677px;top:2320px;width:523px;height:473px;background:linear-gradient(160deg,#7d6c5b 0%,#b7ab9d 40%,#e8e5e0 65%,#c44a45 100%)" role="img" aria-label="Hands holding a tablet beside a small model house on blueprints"></div>
</section>

<section class="why">
  <span class="center-tag" style="top:2868px;color:var(--red);font-size:15px">Why Us</span>
  <h2 class="center-tag" style="top:2898px;font-size:31px;font-weight:700">Your Property, Our Priority</h2>
  <p class="center-tag" style="top:2942px;font-size:12.5px;line-height:19px;color:#c4c4c4;left:320px;width:560px">lorem ipsum dolor sit amet, consectetur adipiscing elit. Nunc vulputate libero et velit interdum, ac aliquet odio mattis.</p>

  <svg class="abs" style="left:354px;top:3035px" width="480" height="480" viewBox="0 0 480 480">
    <circle cx="240" cy="240" r="238" fill="#fbf7f6" stroke="#eee" stroke-width="2"/>
    <circle cx="240" cy="240" r="190" fill="#fff"/>
    <circle cx="240" cy="240" r="180" fill="none" stroke="#eadcd8" stroke-width="18"/>
  </svg>
  <div class="abs" style="left:435px;top:3116px;width:318px;height:318px;border-radius:50%;background:radial-gradient(circle at 50% 55%,#e6b04a 0%,#a6c95a 45%,#5e9a35 100%)" role="img" aria-label="Small model house with a red for-rent tag on green grass"></div>

  <div class="pill" style="left:282px;top:3046px;width:179px">Accounting<br>Services
    <svg width="30" height="28" viewBox="0 0 30 28"><rect x="2" y="14" width="5" height="12" fill="var(--red)"/><rect x="10" y="8" width="5" height="18" fill="var(--red)"/><circle cx="22" cy="12" r="6" fill="none" stroke="var(--red)" stroke-width="2.5"/><path d="M26 16l4 5" stroke="var(--red)" stroke-width="2.5"/></svg></div>
  <div class="pill" style="left:730px;top:3046px;width:180px">
    <svg width="32" height="24" viewBox="0 0 32 24"><path d="M2 18h10l8-6 4 2-8 8H2z" fill="var(--red)"/><path d="M14 2l6 6-4 4-6-6z" fill="var(--red)"/></svg>Leasing</div>
  <div class="pill" style="left:190px;top:3228px;width:179px">Mortgage Utility<br>Payments
    <svg width="30" height="32" viewBox="0 0 30 32"><path d="M10 2h10l-3 6h-4z" fill="var(--red)"/><circle cx="15" cy="20" r="11" fill="var(--red)"/><text x="15" y="25" font-size="13" fill="#fff" text-anchor="middle" font-family="Poppins,sans-serif">$</text></svg></div>
  <div class="pill" style="left:800px;top:3228px;width:179px">
    <svg width="24" height="30" viewBox="0 0 24 30"><path d="M6 13V8a6 6 0 0 1 12 0v5" stroke="var(--red)" stroke-width="3" fill="none"/><rect x="1" y="13" width="22" height="16" rx="2" fill="var(--red)"/><circle cx="12" cy="21" r="2.5" fill="#fff"/></svg>Security<br>Deposits</div>
  <div class="pill" style="left:265px;top:3401px;width:180px">Rent<br>Collections
    <svg width="32" height="30" viewBox="0 0 32 30"><path d="M16 1L1 14h4v15h8v-9h6v9h8V14h4z" fill="var(--red)"/></svg></div>
  <div class="pill" style="left:739px;top:3401px;width:179px">
    <svg width="32" height="32" viewBox="0 0 32 32"><circle cx="13" cy="13" r="10" fill="none" stroke="var(--red)" stroke-width="3"/><path d="M21 21l9 9" stroke="var(--red)" stroke-width="4"/><path d="M9 14l6-5 1 6z" fill="var(--red)"/></svg>Inspections<br>of Property</div>
  <div class="pill" style="left:475px;top:3503px;width:243px;height:80px;flex-direction:column;gap:4px">
    <svg width="30" height="30" viewBox="0 0 30 30"><path d="M4 4l22 22M26 4L4 26" stroke="var(--red)" stroke-width="4" stroke-linecap="round"/></svg>Repair &amp; Maintenance Service</div>
</section>

<section class="contact">
  <span class="tag" style="left:98px;top:3870px">Contact Us</span>
  <h2 class="heading" style="left:98px;top:3896px;line-height:39px">Get in Touch with Brighthold<br>We're Here to Help</h2>
  <form class="form-card">
    <label style="top:22px">Name</label><div class="field" style="top:44px">Your name</div>
    <label style="top:104px">Email</label><div class="field" style="top:126px">Email</div>
    <label style="top:186px">Phone</label><div class="field" style="top:208px">phone number</div>
    <label style="top:270px">Message</label><div class="field" style="top:294px;height:84px">Write message</div>
    <div class="submit">Submit</div>
  </form>
</section>

<section class="testimonials">
  <span class="center-tag" style="top:4286px;color:var(--red);font-size:15px">Testimonials</span>
  <h2 class="center-tag" style="top:4316px;font-size:31px;font-weight:700">Hear from Our Satisfied Clients</h2>
  <p class="center-tag" style="top:4360px;font-size:12.5px;line-height:19px;color:#c4c4c4;left:300px;width:600px">lorem ipsum dolor sit amet, consectetur adipiscing elit. Nunc vulputate libero et velit interdum, ac aliquet odio mattis.</p>
  <div class="arrow" style="left:80px"><svg width="40" height="40" viewBox="0 0 40 40"><path d="M23 13l-7 7 7 7" stroke="#fff" stroke-width="2.5" fill="none"/></svg></div>
  <div class="arrow" style="left:1078px"><svg width="40" height="40" viewBox="0 0 40 40"><path d="M17 13l7 7-7 7" stroke="#fff" stroke-width="2.5" fill="none"/></svg></div>

  <div class="quote" style="left:163px"><div class="stars">★★★★★</div><p>Slate helps you see how many more days you need to work to reach your financial goal.</p><div class="avatar" style="background:#c9a88c" role="img" aria-label="Client portrait"></div><div class="who"><b>Regina</b><br>Founder of XYZ Corp</div></div>
  <div class="quote" style="left:463px"><div class="stars">★★★★★</div><p>Slate helps you see how many more days you need to work to reach your financial goal.</p><div class="avatar" style="background:#3c3431" role="img" aria-label="Client portrait"></div><div class="who"><b>Adam</b><br>CEO</div></div>
  <div class="quote" style="left:761px"><div class="stars">★★★★★</div><p>Slate helps you see how many more days you need to work to reach your financial goal.</p><div class="avatar" style="background:#b9b3c4" role="img" aria-label="Client portrait"></div><div class="who"><b>Miles</b><br>Business owner</div></div>
</section>

<footer class="footer">
  <div class="name"><i></i>BRIGHTHOLD</div>
  <h4 style="left:1000px;top:106px">Get In Touch</h4>
  <span class="social" style="left:1003px" aria-label="Video channel"></span>
  <span class="social" style="left:1037px" aria-label="Social page"></span>
  <span class="social" style="left:1071px" aria-label="Professional profile"></span>
  <div class="rule"></div>

  <h4 style="left:100px;top:248px">Pages</h4>
  <ul style="left:100px;top:274px"><li>Listings</li><li>Owners</li><li>Prospect Tenants</li><li>About</li><li>Community</li><li>Mortgage Info</li></ul>
  <h4 style="left:263px;top:248px">Legal</h4>
  <ul style="left:263px;top:274px"><li>Imprint</li><li>Terms&amp; Condition</li><li>Privacy</li><li>Cookies</li></ul>
  <h4 style="left:424px;top:248px">Contact Info</h4>
  <div class="fcontact" style="top:288px"><svg width="14" height="11" viewBox="0 0 24 18"><rect width="24" height="18" rx="2" fill="#ddd"/><path d="M2 2l10 8 10-8" stroke="#2e2e2e" stroke-width="2" fill="none"/></svg>Tomwhit23@Mailbox.Com</div>
  <div class="fcontact" style="top:320px"><svg width="13" height="13" viewBox="0 0 24 24"><path fill="#ddd" d="M6.6 10.8a15 15 0 0 0 6.6 6.6l2.2-2.2a1 1 0 0 1 1-.25 11.4 11.4 0 0 0 3.6.6 1 1 0 0 1 1 1V20a1 1 0 0 1-1 1A17 17 0 0 1 3 4a1 1 0 0 1 1-1h3.5a1 1 0 0 1 1 1c0 1.25.2 2.45.6 3.6a1 1 0 0 1-.25 1z"/></svg><span>Cell (555) 318-4420<br>Offc. (555) 214-7730</span></div>
  <div class="fcontact" style="top:356px"><svg width="13" height="16" viewBox="0 0 24 30"><path d="M12 0a10 10 0 0 0-10 10c0 8 10 20 10 20s10-12 10-20A10 10 0 0 0 12 0z" fill="#ddd"/><circle cx="12" cy="10" r="4" fill="#2e2e2e"/></svg><span>Brighthold Property<br>Management Inc.<br>480 Lindenwood Ave. #12<br>Fairbrook, CA. 90417</span></div>
  <h4 style="left:730px;top:248px;font-size:12px">Stay Connected</h4>
  <span class="abs" style="left:730px;top:278px;font-size:9px;color:#bbb">Get In Touch</span>
  <div class="sub-input">Enter Your Email</div>
  <div class="sub-btn">Subscribe</div>
  <div class="copy">© 2024 Brighthold All Rights Reserved.</div>
</footer>

</body>
</html>
```